Healthy lifestyle Influencer business card

I need your creativity to have a business card that I can leave in all the restaurants, hotels and spas I visit to inform them that I am an influencer specializing in the wellness sector and that I will write a review about them. You can use my instagram photos Lunavita27 or on my website www.piattileggeriorto.it. I would like my business card to impress with its creativity! thank you very much!

Contact Information for Business Card

siteweb, instagram, phone number

Font styles to use
Decorative
Script

Colors
0094D4
00A9DD
6FCCEA
C7EBF8
E9F6FB
59FF00
82FF00
B8FF75
E3FFCB
F4FFEA
FFC000
F8CF3A
FAE287
FDF2CF
FEFAEE
F0912C
F2A743
F7CA91
FBE8D2
FDF5EE
EE7325
F08F49
F5BC92
FAE3D3
FDF4ED
EB3D1F
EC4F4E
F09395
F8D3D4
FCEDEE
E54698
E96AAD
F1A4CE
F9D9EA
FCEFF6

Requirements
Nice to have
• creativity

```html
<!DOCTYPE html>
<html lang="it">
<head>
<meta charset="utf-8">
<title>Lunavita Gusto – Biglietto da visita</title>
<link rel="stylesheet" href="https://fonts.googleapis.com/css2?family=Great+Vibes&family=Jost:wght@400&family=Roboto:wght@300&display=swap">
<style>
  :root {
    --backdrop: #2b2b2b;
    --sage: #8fbfb1;
    --sage-deep: #7aa99b;
    --sage-soft: #a6cfc3;
    --paper: #f2f2f1;
    --ink: #3a3a3a;
    --ink-soft: #555;
    --icon: #8fbfb1;
  }
  * { margin: 0; padding: 0; box-sizing: border-box; }
  html, body { width: 1200px; height: 1138px; overflow: hidden; background: var(--backdrop); }
  .canvas { position: relative; width: 1200px; height: 1138px; }

  .card { position: absolute; width: 622px; height: 376px; border-radius: 18px; overflow: hidden; }
  .card--front { left: 272px; top: 184px; }
  .card--back { left: 274px; top: 606px; background: var(--paper); }

  .food-grid {
    position: absolute; inset: 0;
    background: linear-gradient(135deg, var(--sage-soft) 0%, var(--sage) 55%, var(--sage-deep) 100%);
  }

  .brand { position: absolute; text-align: center; color: var(--ink); }
  .brand__name { font-family: "Great Vibes", cursive; font-weight: 400; line-height: 1; white-space: nowrap; }
  .brand__tagline { font-family: "Jost", sans-serif; font-weight: 400; white-space: nowrap; }

  .card--front .brand { left: 0; right: 0; top: 138px; }
  .card--front .brand__name { font-size: 64px; }
  .card--front .brand__tagline { font-size: 20px; margin-top: 10px; }

  .social {
    position: absolute; display: flex; align-items: center; gap: 10px;
    font-family: "Roboto", sans-serif; font-weight: 300; font-size: 17px; color: var(--ink);
  }
  .social__dot { width: 14px; height: 14px; border-radius: 50%; background: var(--ink-soft); }
  .card--front .social { left: 0; right: 0; justify-content: center; top: 326px; }

  .card--back .brand { left: 30px; width: 280px; top: 80px; }
  .card--back .brand__name { font-size: 44px; }
  .card--back .brand__tagline { font-size: 15px; margin-top: 8px; }

  .accent-circle {
    position: absolute; left: 400px; top: 40px; width: 260px; height: 260px;
    border-radius: 50%; border: 4px solid var(--sage); opacity: 0.55;
  }

  .person {
    position: absolute; left: 26px; top: 208px;
    font-family: "Great Vibes", cursive; font-size: 42px; color: var(--ink); white-space: nowrap;
  }

  .contacts { position: absolute; left: 44px; top: 266px; list-style: none; }
  .contacts li {
    display: flex; align-items: center; gap: 12px; height: 24px;
    font-family: "Roboto", sans-serif; font-weight: 300; font-size: 17px; color: var(--ink-soft);
  }
  .contacts svg { width: 14px; height: 14px; fill: var(--icon); flex: none; }

  .card--back .social { left: 414px; top: 314px; }
</style>
</head>
<body>
<main class="canvas">

  <section class="card card--front">
    <div class="food-grid" role="img" aria-label="Griglia di foto di piatti sani con velatura verde salvia"></div>
    <div class="brand">
      <p class="brand__name">Lunavita Gusto</p>
      <p class="brand__tagline">Ricette leggere, sapori veri</p>
    </div>
    <p class="social"><span class="social__dot"></span>@Lunavita27</p>
  </section>

  <section class="card card--back">
    <div class="accent-circle"></div>
    <div class="brand">
      <p class="brand__name">Lunavita Gusto</p>
      <p class="brand__tagline">Ricette leggere, sapori veri</p>
    </div>
    <p class="person">Luna Ventresca</p>
    <ul class="contacts">
      <li>
        <svg viewBox="0 0 16 16" aria-hidden="true"><path d="M1 5c0-2 3-3 7-3s7 1 7 3v1h-4V5H5v1H1z M3 7h10l1 7H2z"/></svg>
        000-0000-0000
      </li>
      <li>
        <svg viewBox="0 0 16 16" aria-hidden="true"><path d="M1 3h14v10H1z M2 4l6 5 6-5" stroke="#f2f2f1" stroke-width="1.2"/></svg>
        info@piattileggeriorto.it
      </li>
      <li>
        <svg viewBox="0 0 16 16" aria-hidden="true"><circle cx="8" cy="8" r="7"/><path d="M1 8h14M8 1v14M3 4h10M3 12h10" stroke="#f2f2f1" stroke-width="1" fill="none"/></svg>
        www.piattileggeriorto.it
      </li>
    </ul>
    <p class="social"><span class="social__dot"></span>@Lunavita27</p>
  </section>

</main>
</body>
</html>
```